Colin Vardek Business card

Hey there, I’m hoping to have a business card designed. I’m in Real estate and just switched to a new Brokerage called: The Harbourline Property Group

The back could just be the company name maybe or whatever looks good!

I’ve attached some logos of our company and some cards my buddy had done up.

On the card:
Colin Vardek
colinvardek@mailora.com
587-412-9065
colinvardek.ca

Target Market(s)

Home buyers and sellers

Industry/Entity Type

Real Estate

Contact Information for Business Card

just looking for a cool and modern design with my picture on it. I like the idea of Black and red being used.

Requirements
Must have
• all the details provided. I'm open to anything. Just want a professional looking card.

```html
<!DOCTYPE html>
<html lang="en">
<head>
<meta charset="utf-8">
<title>Colin Vardek – Business Card</title>
<link rel="stylesheet" href="https://fonts.googleapis.com/css2?family=Montserrat:wght@700;800&family=Lato:wght@400&display=swap">
<style>
  :root {
    --page-bg: #f2f2f2;
    --card-white: #ffffff;
    --ink: #0a0a0c;
    --brand-red: #cc1f3a;
    --photo-dark: #2b313b;
    --photo-light: #d9dbe0;
  }
  * { box-sizing: border-box; margin: 0; padding: 0; }
  html, body {
    width: 1200px; height: 1059px; overflow: hidden;
    background: var(--page-bg);
  }
  .canvas { position: relative; width: 1200px; height: 1059px; }

  .card { position: absolute; left: 245px; width: 706px; height: 405px; overflow: hidden; }
  .card--front { top: 82px; background: var(--card-white); }
  .card--back { top: 565px; background: var(--ink); display: flex; align-items: center; justify-content: center; }

  .brand-name {
    font-family: "Montserrat", sans-serif;
    font-weight: 800;
    text-transform: uppercase;
    line-height: 1.05;
    letter-spacing: 0.5px;
  }
  .card--front .brand-name {
    position: absolute; left: 48px; top: 36px;
    color: var(--ink); font-size: 31px;
  }
  .card--back .brand-name {
    color: var(--card-white); font-size: 50px; text-align: center;
  }

  .agent-photo {
    position: absolute; left: 499px; top: 24px; width: 204px; height: 318px;
    background: linear-gradient(180deg, var(--photo-light) 0%, var(--photo-dark) 45%, var(--photo-dark) 100%);
    clip-path: polygon(35% 0, 65% 0, 70% 25%, 100% 40%, 100% 100%, 0 100%, 4% 45%, 30% 25%);
  }

  .card-bands { position: absolute; left: 0; top: 0; width: 706px; height: 405px; }

  .agent-name {
    font-family: "Montserrat", sans-serif; font-weight: 700;
    color: var(--brand-red); font-size: 26px; line-height: 1;
    position: absolute;
  }
  .agent-name--main { left: 46px; top: 242px; }
  .agent-name--band { right: 62px; top: 362px; }

  .contact-list { position: absolute; left: 40px; top: 282px; list-style: none; }
  .contact-item {
    display: flex; align-items: center; gap: 11px;
    font-family: "Lato", sans-serif; font-size: 18.5px; color: var(--ink);
    height: 25px;
  }
  .contact-icon { width: 19px; height: 19px; flex: none; fill: var(--brand-red); }
</style>
</head>
<body>
<main class="canvas">
  <section class="card card--front" aria-label="Business card front">
    <div class="brand-name">The Harbourline<br>Property Group</div>

    <div class="agent-photo" role="img" aria-label="Portrait photo of Colin Vardek in a dark suit and white shirt"></div>

    <svg class="card-bands" viewBox="0 0 706 405" aria-hidden="true">
      <polygon points="0,382 350,382 331,405 0,405" fill="#cc1f3a"/>
      <polygon points="387,342 706,340 706,405 337,405" fill="#0a0a0c"/>
    </svg>

    <h1 class="agent-name agent-name--main">Colin Vardek</h1>
    <ul class="contact-list">
      <li class="contact-item">
        <svg class="contact-icon" viewBox="0 0 24 24"><path d="M6.6 2.5l3 4.2-2 2.2c1.2 2.6 3.3 4.8 6 6l2.2-2 4.2 3-1.8 4.1C9.8 20.2 3.8 14.2 2.5 5.8z"/></svg>
        <span>587-412-9065</span>
      </li>
      <li class="contact-item">
        <svg class="contact-icon" viewBox="0 0 24 24"><path d="M2 5h20v14H2z M2 5l10 8 10-8" fill="#cc1f3a"/><path d="M3 6l9 7 9-7" fill="none" stroke="#fff" stroke-width="1.8"/></svg>
        <span>colinvardek@mailora.com</span>
      </li>
      <li class="contact-item">
        <svg class="contact-icon" viewBox="0 0 24 24"><circle cx="12" cy="12" r="10"/><path d="M12 2v20M2 12h20M5 6c4 2 10 2 14 0M5 18c4-2 10-2 14 0" fill="none" stroke="#fff" stroke-width="1.4"/></svg>
        <span>colinvardek.ca</span>
      </li>
    </ul>

    <p class="agent-name agent-name--band">Colin Vardek</p>
  </section>

  <section class="card card--back" aria-label="Business card back">
    <div class="brand-name">The Harbourline<br>Property Group</div>
  </section>
</main>
</body>
</html>
```